Business Card Design - Photographer

I am a landscape photographer and I require a business card design. 

I require two designs:
1)  a double sided business card
 and
b)  a single sided business card 

The single sided design can either be the same as the double sided (with just one side having all the information)....or it can be an entire new design. Its up to you.

My corporate colours are (CMYK):

Blue   69, 32, 0, 0
Grey  72,  64,  47,  31
Green  32,  2,  91,  0
Yellow   0, 19, 92, 0
Orange  0, 39, 75, 0

Colour space in final file should be in CMYK.

The details that need to be included on the card:

- Use the provided Logo
- Name: Wiktor Baranowski
- Email:   sales@vistalumeworks.com.au
- Website:    vistalumeworks.com.au
- Twitter:    twitter.com/vistalumeworks
- Facebook:   facebook.com/vistalumeworks
- Mobile  0417 539 662

Please use the attached template to design the logo to the specified size, including the marked bleed lines. I have also attached my logo in PNG (transparent background) and ai format for you to use.

The final file should be:
- Photoshop version with layers so I can edit the name/text etc. All non vector files should be high resolution at 1039 x 697 pixels at 300 dpi.

I also require a file as:
- Vector based PDF

Anyway questions please contact me.

Thank you

Industry/Entity Type

Landscape

Logo styles of interest
Pictorial/Combination Logo
Abstract Logo
Wordmark Logo
Lettermark Logo
Requirements
Must have
• The details that need to be included on the card:

- Use the provided Logo
- Name: Wiktor Baranowski
- Email: sales@vistalumeworks.com.au
- Website: vistalumeworks.com.au
- Twitter: twitter.com/vistalumeworks
- Facebook: facebook.com/vistalumeworks
- Mobile 0417 539 662

```html
<!DOCTYPE html>
<html lang="en">
<head>
<meta charset="utf-8">
<title>Vistalume Works – Business Card</title>
<link rel="stylesheet" href="https://fonts.googleapis.com/css2?family=Cinzel:wght@400;600;700&display=swap">
<style>
  :root {
    --backdrop: #808184;
    --card: #ffffff;
    --brand-blue: #3d90d0;
    --brand-orange: #f8a647;
    --brand-grey: #3b3d4f;
    --on-blue: #ffffff;
  }
  * { margin: 0; padding: 0; box-sizing: border-box; }
  html, body {
    width: 1200px; height: 736px; overflow: hidden;
    background: var(--backdrop);
  }
  .canvas { position: relative; width: 1200px; height: 736px; }
  .card {
    position: absolute; left: 123px; top: 110px;
    width: 937px; height: 535px;
    border-radius: 46px; overflow: hidden;
    background: var(--card);
  }
  .card__shapes { position: absolute; inset: 0; }
  .brand {
    position: absolute; left: 40px; top: 250px; width: 395px;
    display: flex; align-items: center; justify-content: center; gap: 14px;
  }
  .brand__dot {
    width: 22px; height: 22px; border-radius: 50%;
    background: var(--brand-grey);
  }
  .brand__name {
    font-family: "Cinzel", serif; font-weight: 700;
    font-size: 32px; letter-spacing: 0.5px;
    color: var(--brand-grey); white-space: nowrap;
  }
  .website {
    position: absolute; left: 30px; top: 422px; width: 415px;
    text-align: center; white-space: nowrap;
    font-family: "Cinzel", serif; font-weight: 600;
    color: var(--brand-blue); font-size: 17px;
  }
  .website__domain { font-size: 22px; }
  .contacts {
    position: absolute; left: 520px; top: 216px; width: 420px;
    list-style: none; text-align: center;
    font-family: "Cinzel", serif; font-weight: 400;
    font-size: 17.5px; color: var(--on-blue);
  }
  .contacts li { height: 41px; line-height: 30px; white-space: nowrap; }
</style>
</head>
<body>
<div class="canvas">
  <section class="card" aria-label="Business card">
    <svg class="card__shapes" width="937" height="535" viewBox="0 0 937 535" aria-hidden="true">
      <circle class="arc-orange" cx="848" cy="268" r="381" fill="var(--brand-orange)"/>
      <circle class="arc-gap" cx="866" cy="268" r="386" fill="var(--card)"/>
      <circle class="panel-blue" cx="961" cy="268" r="452" fill="var(--brand-blue)"/>
    </svg>

    <div class="brand">
      <span class="brand__dot"></span>
      <span class="brand__name">VISTALUME WORKS</span>
    </div>

    <p class="website">www.<span class="website__domain">VISTALUMEWORKS</span>.com.au</p>

    <ul class="contacts">
      <li>E : sales@vistalumeworks.com.au</li>
      <li>T : twitter.com/vistalumeworks</li>
      <li>F : facebook.com/vistalumeworks</li>
      <li>M : 0417 539 662</li>
    </ul>
  </section>
</div>
</body>
</html>
```